Blog Design for global news commentary

Need a very simple blog template (see attachment, Frontpage) that includes entries and ability to upload photos/video. Tabs are not needed (See Marlow Tearoom Provincial blog for sort of what I am going for but a lot less cluttered). A section that can access old entries is needed as well as a "contact me" tab. The format should be very simple. An entry and section for comments, new entry, section for comments etc. comments sections should be able to be monitored by me. With the ability for readers to contribute via quidlane. The look and feel should be sophisticated and should target an educated global audience. The blog is all about commenting on global news around the world. For example, a news article could be photographed and then commented on. Type face should be simple, clean and 1930's style. See Harbor Ledger magazine for looks and feel. If viewers wish to contribute they can make donations via quidlane on the site. Once the template is competed it should be very easy for me to update and work with and handed over to a web hosting service. I own the domain name which I want to use. It would be best to use an existing template eg wordpress. So in simple terms need a wordpress template adapted for this blog idea. Not sure what coded vs. uncoded means. But the overall objective is very simple. Template should be clean, no design elements other than the name of the blog.

Target Market(s)

Educated people from around the world interested in current events

Industry/Entity Type

News

Number of Pages Required

2 page

Other font styles liked:
• Upper East Side

Colors
0255a3
1b1b1b
5c5c5c

Requirements
Must have
• This is a blog so it should have all the standard features including daily updates, photo/video upload, comments that can be monitored by me, quidlane donation link. It should be easy for me to use and handle once completed and delivered to web host. It must have a simple, elegant look and feel. I have chose Serif font style but recommend a 1930's Art Deco - clean, unfussy type face. Type face Upper East Side is what I am looking for
Nice to have
• The look must be simple and no pictures, design elements or logos. Clean and crisp
Should not have
• Any pictures for illustrations as part of the overall design

```html
<!DOCTYPE html>
<html lang="en">
<head>
<meta charset="utf-8">
<title>Meridian Notes</title>
<link rel="stylesheet" href="https://fonts.googleapis.com/css2?family=Poiret+One&family=Open+Sans:wght@400;600&display=swap">
<style>
:root{
  --blue:#0255a3;
  --ink:#1b1b1b;
  --grey:#5c5c5c;
  --light:#f1f1f1;
  --line:#dcdcdc;
  --orange:#f2a23a;
  --white:#ffffff;
}
*{box-sizing:border-box;margin:0;padding:0}
html,body{width:1200px;height:2260px;overflow:hidden;background:var(--white)}
body{font-family:"Open Sans",Arial,sans-serif;color:var(--grey);font-size:11px;position:relative}
.wrap{position:absolute;left:232px;width:736px}
.display{font-family:"Poiret One","Georgia",serif;color:var(--ink);font-weight:400}

/* header */
.site-header{top:28px;height:40px;display:flex;justify-content:space-between;align-items:center}
.brand{font-family:"Poiret One",serif;font-size:36px;color:var(--blue);letter-spacing:1px}
.account{display:flex;align-items:center;gap:8px;font-size:10px}
.account .search{width:110px;height:20px;border:1px solid var(--line);padding:0 6px;line-height:18px;color:#999}
.account .btn{height:20px;padding:0 10px;line-height:20px;color:var(--white);font-weight:600}
.btn-blue{background:var(--blue)}
.btn-orange{background:var(--orange)}

.main-nav{top:74px;height:24px;background:var(--ink);display:flex;align-items:center}
.main-nav a{color:#e6e6e6;text-decoration:none;font-size:10px;padding:0 14px;line-height:24px}
.main-nav a.current{background:#333}
.main-nav a.subscribe{margin-left:auto;background:var(--blue);color:var(--white)}

/* hero */
.hero{top:104px;height:262px}
.hero .media{position:absolute;inset:0;background:linear-gradient(160deg,#cfe0c4 0%,#8fa88a 40%,#5a6a56 75%,#3d4a3b 100%)}
.hero .caption{position:absolute;left:18px;bottom:16px;background:rgba(0,0,0,.55);padding:6px 12px;font-size:28px;color:var(--white)}

/* feature */
.feature{top:398px;height:210px;background:var(--ink);display:flex}
.feature .media{width:480px;height:210px;background:linear-gradient(135deg,#3b4a5a,#1f2933 55%,#6b5a3a)}
.feature .body{flex:1;padding:20px 22px;color:#cfcfcf}
.feature h2{color:var(--white);font-size:26px;line-height:1.2;margin-bottom:12px}
.feature p{font-size:10px;line-height:1.6;margin-bottom:14px}

/* meta */
.meta{display:flex;gap:14px;align-items:center;font-size:9px;color:#8a8a8a}
.meta span{display:flex;align-items:center;gap:4px}
.meta svg{width:9px;height:9px}

/* grid cards */
.grid{display:grid;grid-template-columns:repeat(3,232px);column-gap:20px}
.grid-row-1{top:628px}
.grid-row-2{top:958px}
.card .media{height:132px;position:relative}
.card .body{background:var(--light);padding:12px 14px;height:176px}
.card h3{font-size:22px;line-height:1.15;margin-bottom:8px}
.card p{font-size:9.5px;line-height:1.6;margin-bottom:10px}
.play{position:absolute;left:50%;top:50%;width:28px;height:28px;margin:-14px 0 0 -14px}

.rule{top:1300px;height:4px;background:var(--ink)}

.section-title{font-family:"Poiret One",serif;font-size:30px;color:var(--blue)}
.recent-title{top:1330px}
.commented-title{top:1758px}

.mini{display:grid;grid-template-columns:repeat(4,172px);column-gap:16px}
.mini-recent{top:1376px}
.mini-commented{top:1804px}
.mini .media{height:112px}
.mini .body{background:var(--light);padding:10px 10px;height:170px}
.mini h3{font-size:19px;line-height:1.15;margin-bottom:8px}
.mini p{font-size:9px;line-height:1.55;margin-bottom:8px}

/* newsletter */
.newsletter{top:1690px;height:40px;background:#000;display:flex;align-items:center;padding:0 16px;gap:14px}
.newsletter .label{font-family:"Poiret One",serif;color:var(--white);font-size:24px;margin-right:auto}
.newsletter .field{width:300px;height:22px;background:var(--white);padding:0 8px;line-height:22px;font-size:10px;color:#999}
.newsletter .btn{height:22px;line-height:22px;padding:0 14px;background:var(--blue);color:var(--white);font-size:10px;font-weight:600}

/* footer */
.site-footer{position:absolute;left:0;top:2136px;width:1200px;height:124px;background:#000;text-align:center;color:#9a9a9a}
.footer-links{padding-top:28px;font-size:9px}
.footer-links a{color:#cfcfcf;text-decoration:none;margin:0 6px}
.copyright{margin-top:8px;font-size:9px}
.social{margin-top:12px;display:flex;justify-content:center;gap:6px}
.social i{width:14px;height:14px;border-radius:50%;display:block}
</style>
</head>
<body>

<header class="wrap site-header">
  <div class="brand">Meridian Notes</div>
  <div class="account">
    <span>Login</span><span>|</span><span>Register</span>
    <span class="search">Search</span>
    <span class="btn btn-blue">Register</span>
    <span class="btn btn-orange">Donate</span>
  </div>
</header>

<nav class="wrap main-nav">
  <a class="current">Home</a><a>World</a><a>Europe</a><a>Asia</a><a>Americas</a><a>Africa</a><a>Markets</a><a>Opinion</a><a>Archive</a><a>Contact</a>
  <a class="subscribe">Subscribe</a>
</nav>

<section class="wrap hero">
  <div class="media" role="img" aria-label="Photo of runners on a city street"></div>
  <div class="caption display" style="color:#fff">Runners take the city streets</div>
</section>

<section class="wrap feature">
  <div class="media" role="img" aria-label="Photo of reporters and a camera in a television studio"></div>
  <div class="body">
    <h2 class="display" style="color:#fff">Across the wire, a studio view</h2>
    <p>A short reflection on how the evening broadcast shaped the week's debate across several capitals.</p>
    <div class="meta">
      <span><svg viewBox="0 0 10 10"><circle cx="5" cy="5" r="4" fill="none" stroke="#8a8a8a"/><path d="M5 2.5V5h2" fill="none" stroke="#8a8a8a"/></svg>14 June</span>
      <span><svg viewBox="0 0 10 10"><path d="M1 1h8v6H4L2 9V7H1z" fill="#8a8a8a"/></svg>6</span>
    </div>
  </div>
</section>

<section class="wrap grid grid-row-1">
  <article class="card">
    <div class="media" role="img" aria-label="Photo of a crowd at a concert" style="background:linear-gradient(135deg,#7a2a2a,#2a1a2a)"></div>
    <div class="body"><h3 class="display">Quiet talks at the border crossing</h3><p>A brief commentary on the day's reporting, with notes on sources and what comes next.</p>
    <div class="meta"><span><svg viewBox="0 0 10 10"><circle cx="5" cy="5" r="4" fill="none" stroke="#8a8a8a"/><path d="M5 2.5V5h2" fill="none" stroke="#8a8a8a"/></svg>14 June</span><span><svg viewBox="0 0 10 10"><path d="M1 1h8v6H4L2 9V7H1z" fill="#8a8a8a"/></svg>6</span></div></div>
  </article>
  <article class="card">
    <div class="media" role="img" aria-label="Photo of a music performance on stage" style="background:linear-gradient(135deg,#5a4a6a,#2a2030)"></div>
    <div class="body"><h3 class="display">What the summit left unsaid</h3><p>A brief commentary on the day's reporting, with notes on sources and what comes next.</p>
    <div class="meta"><span><svg viewBox="0 0 10 10"><circle cx="5" cy="5" r="4" fill="none" stroke="#8a8a8a"/><path d="M5 2.5V5h2" fill="none" stroke="#8a8a8a"/></svg>14 June</span><span><svg viewBox="0 0 10 10"><path d="M1 1h8v6H4L2 9V7H1z" fill="#8a8a8a"/></svg>6</span></div></div>
  </article>
  <article class="card">
    <div class="media" role="img" aria-label="Video still of a live stage event" style="background:linear-gradient(135deg,#3a3a5a,#1a1a24)">
      <svg class="play" viewBox="0 0 28 28"><circle cx="14" cy="14" r="13" fill="#0255a3"/><path d="M11 8l9 6-9 6z" fill="#fff"/></svg>
    </div>
    <div class="body"><h3 class="display">Voices from the campaign trail</h3><p>A brief commentary on the day's reporting, with notes on sources and what comes next.</p>
    <div class="meta"><span><svg viewBox="0 0 10 10"><circle cx="5" cy="5" r="4" fill="none" stroke="#8a8a8a"/><path d="M5 2.5V5h2" fill="none" stroke="#8a8a8a"/></svg>14 June</span><span><svg viewBox="0 0 10 10"><path d="M1 1h8v6H4L2 9V7H1z" fill="#8a8a8a"/></svg>6</span></div></div>
  </article>
</section>

<section class="wrap grid grid-row-2">
  <article class="card">
    <div class="media" role="img" aria-label="Photo of a speaker addressing an audience" style="background:linear-gradient(135deg,#6a4a3a,#2a2220)"></div>
    <div class="body"><h3 class="display">A speech that changed the room</h3><p>A brief commentary on the day's reporting, with notes on sources and what comes next.</p>
    <div class="meta"><span><svg viewBox="0 0 10 10"><circle cx="5" cy="5" r="4" fill="none" stroke="#8a8a8a"/><path d="M5 2.5V5h2" fill="none" stroke="#8a8a8a"/></svg>14 June</span><span><svg viewBox="0 0 10 10"><path d="M1 1h8v6H4L2 9V7H1z" fill="#8a8a8a"/></svg>6</span></div></div>
  </article>
  <article class="card">
    <div class="media" role="img" aria-label="Video still of a crowd at a night event" style="background:linear-gradient(135deg,#2a3a6a,#14182a)">
      <svg class="play" viewBox="0 0 28 28"><circle cx="14" cy="14" r="13" fill="#0255a3"/><path d="M11 8l9 6-9 6z" fill="#fff"/></svg>
    </div>
    <div class="body"><h3 class="display">Crowds gather for the night vigil</h3><p>A brief commentary on the day's reporting, with notes on sources and what comes next.</p>
    <div class="meta"><span><svg viewBox="0 0 10 10"><circle cx="5" cy="5" r="4" fill="none" stroke="#8a8a8a"/><path d="M5 2.5V5h2" fill="none" stroke="#8a8a8a"/></svg>14 June</span><span><svg viewBox="0 0 10 10"><path d="M1 1h8v6H4L2 9V7H1z" fill="#8a8a8a"/></svg>6</span></div></div>
  </article>
  <article class="card">
    <div class="media" role="img" aria-label="Photo of a reader at a microphone" style="background:linear-gradient(135deg,#c9c2b8,#6a5a50)"></div>
    <div class="body"><h3 class="display">Poetry readings in a time of strain</h3><p>A brief commentary on the day's reporting, with notes on sources and what comes next.</p>
    <div class="meta"><span><svg viewBox="0 0 10 10"><circle cx="5" cy="5" r="4" fill="none" stroke="#8a8a8a"/><path d="M5 2.5V5h2" fill="none" stroke="#8a8a8a"/></svg>14 June</span><span><svg viewBox="0 0 10 10"><path d="M1 1h8v6H4L2 9V7H1z" fill="#8a8a8a"/></svg>6</span></div></div>
  </article>
</section>

<div class="wrap rule"></div>

<h2 class="wrap section-title recent-title">Recent Post</h2>

<section class="wrap mini mini-recent">
  <article>
    <div class="media" role="img" aria-label="Photo of people on a waterfront" style="background:linear-gradient(135deg,#9a9a9a,#3a3a3a)"></div>
    <div class="body"><h3 class="display">Dawn notes on the harbour strike</h3><p>Short comment on the story, with links to sources and reader notes.</p>
    <div class="meta"><span><svg viewBox="0 0 10 10"><circle cx="5" cy="5" r="4" fill="none" stroke="#8a8a8a"/><path d="M5 2.5V5h2" fill="none" stroke="#8a8a8a"/></svg>14 June</span><span><svg viewBox="0 0 10 10"><path d="M1 1h8v6H4L2 9V7H1z" fill="#8a8a8a"/></svg>6</span></div></div>
  </article>
  <article>
    <div class="media" role="img" aria-label="Photo of a lit night stage" style="background:linear-gradient(135deg,#6a2a8a,#1a102a)"></div>
    <div class="body"><h3 class="display">Night markets and new tariffs</h3><p>Short comment on the story, with links to sources and reader notes.</p>
    <div class="meta"><span><svg viewBox="0 0 10 10"><circle cx="5" cy="5" r="4" fill="none" stroke="#8a8a8a"/><path d="M5 2.5V5h2" fill="none" stroke="#8a8a8a"/></svg>14 June</span><span><svg viewBox="0 0 10 10"><path d="M1 1h8v6H4L2 9V7H1z" fill="#8a8a8a"/></svg>6</span></div></div>
  </article>
  <article>
    <div class="media" role="img" aria-label="Photo of plated food" style="background:linear-gradient(135deg,#c8963a,#6a4a1a)"></div>
    <div class="body"><h3 class="display">Street food as quiet diplomacy</h3><p>Short comment on the story, with links to sources and reader notes.</p>
    <div class="meta"><span><svg viewBox="0 0 10 10"><circle cx="5" cy="5" r="4" fill="none" stroke="#8a8a8a"/><path d="M5 2.5V5h2" fill="none" stroke="#8a8a8a"/></svg>14 June</span><span><svg viewBox="0 0 10 10"><path d="M1 1h8v6H4L2 9V7H1z" fill="#8a8a8a"/></svg>6</span></div></div>
  </article>
  <article>
    <div class="media" role="img" aria-label="Photo of an outdoor gathering in a garden" style="background:linear-gradient(135deg,#8ab0d0,#4a6a4a)"></div>
    <div class="body"><h3 class="display">Garden protests in the old quarter</h3><p>Short comment on the story, with links to sources and reader notes.</p>
    <div class="meta"><span><svg viewBox="0 0 10 10"><circle cx="5" cy="5" r="4" fill="none" stroke="#8a8a8a"/><path d="M5 2.5V5h2" fill="none" stroke="#8a8a8a"/></svg>14 June</span><span><svg viewBox="0 0 10 10"><path d="M1 1h8v6H4L2 9V7H1z" fill="#8a8a8a"/></svg>6</span></div></div>
  </article>
</section>

<section class="wrap newsletter">
  <span class="label">Newsletter Subscribe</span>
  <span class="field">Your email address</span>
  <span class="btn">Subscribe</span>
</section>

<h2 class="wrap section-title commented-title">Most Commented</h2>

<section class="wrap mini mini-commented">
  <article>
    <div class="media" role="img" aria-label="Photo of a stadium crowd at night" style="background:linear-gradient(135deg,#7a3a7a,#20102a)"></div>
    <div class="body"><h3 class="display">Stadium nights and public mood</h3><p>Short comment on the story, with links to sources and reader notes.</p>
    <div class="meta"><span><svg viewBox="0 0 10 10"><circle cx="5" cy="5" r="4" fill="none" stroke="#8a8a8a"/><path d="M5 2.5V5h2" fill="none" stroke="#8a8a8a"/></svg>14 June</span><span><svg viewBox="0 0 10 10"><path d="M1 1h8v6H4L2 9V7H1z" fill="#8a8a8a"/></svg>6</span></div></div>
  </article>
  <article>
    <div class="media" role="img" aria-label="Photo of a set dinner table" style="background:linear-gradient(135deg,#b89a7a,#5a4030)"></div>
    <div class="body"><h3 class="display">Talks resume over the dinner table</h3><p>Short comment on the story, with links to sources and reader notes.</p>
    <div class="meta"><span><svg viewBox="0 0 10 10"><circle cx="5" cy="5" r="4" fill="none" stroke="#8a8a8a"/><path d="M5 2.5V5h2" fill="none" stroke="#8a8a8a"/></svg>14 June</span><span><svg viewBox="0 0 10 10"><path d="M1 1h8v6H4L2 9V7H1z" fill="#8a8a8a"/></svg>6</span></div></div>
  </article>
  <article>
    <div class="media" role="img" aria-label="Photo of a festival crowd" style="background:linear-gradient(135deg,#a04a3a,#3a1a1a)"></div>
    <div class="body"><h3 class="display">The festival that became a forum</h3><p>Short comment on the story, with links to sources and reader notes.</p>
    <div class="meta"><span><svg viewBox="0 0 10 10"><circle cx="5" cy="5" r="4" fill="none" stroke="#8a8a8a"/><path d="M5 2.5V5h2" fill="none" stroke="#8a8a8a"/></svg>14 June</span><span><svg viewBox="0 0 10 10"><path d="M1 1h8v6H4L2 9V7H1z" fill="#8a8a8a"/></svg>6</span></div></div>
  </article>
  <article>
    <div class="media" role="img" aria-label="Photo of white tents on a lawn" style="background:linear-gradient(180deg,#bcd4ea 0%,#e8e8e8 55%,#6a8a4a 100%)"></div>
    <div class="body"><h3 class="display">Tents rise on the palace lawn</h3><p>Short comment on the story, with links to sources and reader notes.</p>
    <div class="meta"><span><svg viewBox="0 0 10 10"><circle cx="5" cy="5" r="4" fill="none" stroke="#8a8a8a"/><path d="M5 2.5V5h2" fill="none" stroke="#8a8a8a"/></svg>14 June</span><span><svg viewBox="0 0 10 10"><path d="M1 1h8v6H4L2 9V7H1z" fill="#8a8a8a"/></svg>6</span></div></div>
  </article>
</section>

<footer class="site-footer">
  <div class="footer-links"><a>Home</a><a>World</a><a>Europe</a><a>Asia</a><a>Americas</a><a>Africa</a><a>Markets</a><a>Opinion</a><a>Archive</a><a>Contact</a></div>
  <div class="copyright">© 2015 Meridian Notes. All rights reserved.</div>
  <div class="social">
    <i style="background:#3b6fb6"></i><i style="background:#2aa3d8"></i><i style="background:#d6453b"></i><i style="background:#c0392b"></i><i style="background:#e0543a"></i><i style="background:#d63a7a"></i><i style="background:#2a7ab0"></i><i style="background:#5c5c5c"></i>
  </div>
</footer>

</body>
</html>
```